Copperleaf Roofing Business Card

This is my current business card. But I’d like to make some changes. Somewhere on the card I’d like to list some of the services we offer. Maybe on the back? But I’d still like to keep the red. White and black modern look.

-residential & commercial roofing
-Roof Repairs & Maintenance
-Storm Damage & Insurance Claims specialist
-Christmas Lights and permanent Christmas lights
Fencing. Windows. Gutters. Siding. Sheetrock, painting.

```html
<!DOCTYPE html>
<html lang="en">
<head>
<meta charset="utf-8">
<title>Copperleaf Roofing Business Card</title>
<link rel="stylesheet" href="https://fonts.googleapis.com/css2?family=Montserrat:wght@600;700;800&family=Poppins:wght@400;500&family=Audiowide&display=swap">
<style>
  :root {
    --stage: #1b1b1b;
    --red: #e3121b;
    --red-deep: #a8000b;
    --red-bright: #f01d22;
    --black: #0b0a0a;
    --black-warm: #2a0506;
    --white: #ffffff;
    --rule: rgba(255,255,255,0.55);
  }
  * { margin: 0; padding: 0; box-sizing: border-box; }
  html, body { width: 1200px; height: 1015px; overflow: hidden; }
  body {
    background: var(--stage);
    position: relative;
    font-family: "Poppins", sans-serif;
  }
  .card {
    position: absolute;
    left: 190px;
    width: 820px;
    height: 469px;
    overflow: hidden;
    box-shadow: 0 10px 30px rgba(0,0,0,0.55);
  }
  .card-back { top: 21px; }
  .card-front { top: 525px; }
  .card-texture { position: absolute; inset: 0; }
  .card-back .card-texture {
    background:
      linear-gradient(90deg, rgba(0,0,0,0) 0%, rgba(0,0,0,0.12) 50%, rgba(0,0,0,0) 100%),
      radial-gradient(ellipse at 30% 70%, var(--red-bright) 0%, var(--red) 45%, var(--red-deep) 100%);
  }
  .card-front .card-texture {
    background:
      radial-gradient(ellipse at 80% 20%, var(--black-warm) 0%, var(--black) 60%),
      var(--black);
  }

  /* Back: services */
  .services {
    position: absolute;
    inset: 0;
    display: flex;
    flex-direction: column;
    align-items: center;
    justify-content: center;
    color: var(--white);
    font-family: "Montserrat", sans-serif;
    font-weight: 700;
    text-transform: uppercase;
    text-align: center;
  }
  .service-list { list-style: none; }
  .service-list li { font-size: 25px; letter-spacing: 0.5px; line-height: 1.55; }
  .service-rule {
    width: 640px; height: 1px; background: var(--rule);
    margin: 16px 0 14px;
  }
  .service-extras { font-size: 18px; font-weight: 600; letter-spacing: 0.6px; }

  /* Front: identity */
  .brand {
    position: absolute;
    right: 60px;
    top: 70px;
    display: flex;
    align-items: center;
    gap: 18px;
  }
  .brand-mark {
    width: 74px; height: 74px; border-radius: 50%;
    background: var(--red);
    border: 3px solid var(--white);
    flex: none;
  }
  .brand-name {
    font-family: "Montserrat", sans-serif;
    font-weight: 800;
    font-size: 40px;
    line-height: 1.05;
    color: var(--white);
    text-transform: uppercase;
    letter-spacing: 1px;
  }
  .holder {
    position: absolute;
    left: 60px;
    right: 60px;
    top: 212px;
  }
  .holder-name {
    font-family: "Audiowide", sans-serif;
    color: var(--red);
    font-size: 32px;
    line-height: 1.2;
    text-transform: uppercase;
    letter-spacing: 1px;
  }
  .holder-line {
    display: flex;
    align-items: center;
    gap: 14px;
    margin-top: 2px;
  }
  .holder-role {
    color: var(--white);
    font-size: 22px;
    letter-spacing: 1px;
    line-height: 1.3;
  }
  .holder-rule {
    flex: 1;
    height: 1px;
    background: var(--red);
  }
  .contacts {
    position: absolute;
    left: 60px;
    top: 345px;
    list-style: none;
    color: var(--white);
    font-size: 25px;
  }
  .contacts li { display: flex; align-items: center; gap: 12px; line-height: 1.6; }
  .contact-icon { width: 30px; height: 30px; flex: none; }
  .website {
    position: absolute;
    right: 60px;
    top: 300px;
    color: var(--white);
    font-size: 24px;
    letter-spacing: 0.5px;
  }
  .website .domain { color: var(--red); }
</style>
</head>
<body>
  <section class="card card-back">
    <div class="card-texture" role="img" aria-label="Red tartan plaid background"></div>
    <div class="services">
      <ul class="service-list">
        <li>Residential &amp; Commercial Roofing</li>
        <li>Roof Repairs &amp; Maintenance</li>
        <li>Storm Damage &amp; Insurance Claims Specialist</li>
        <li>Christmas Lights and Permanent Christmas Lights</li>
      </ul>
      <div class="service-rule"></div>
      <p class="service-extras">Fencing • Windows • Gutters • Siding • Sheetrock • Painting.</p>
    </div>
  </section>

  <section class="card card-front">
    <div class="card-texture" role="img" aria-label="Dark black and red tartan plaid background"></div>
    <div class="brand">
      <span class="brand-mark"></span>
      <p class="brand-name">Copperleaf<br>Roofing Co.</p>
    </div>
    <div class="holder">
      <p class="holder-name">Dale Mercer</p>
      <div class="holder-line">
        <p class="holder-role">OWNER</p>
        <span class="holder-rule"></span>
      </div>
    </div>
    <p class="website">www.<span class="domain">copperleafroofing</span>.co</p>
    <ul class="contacts">
      <li>
        <svg class="contact-icon" viewBox="0 0 30 30" aria-hidden="true">
          <circle cx="15" cy="15" r="15" fill="var(--red)"/>
          <path d="M10 8c1-1 2 0 3 2s0 2-1 3c1 2 2 3 4 4 1-1 1-2 3-1s3 2 2 3c-1 2-3 3-6 1-3-2-5-4-6-7-1-2 0-4 1-5z" fill="var(--white)"/>
        </svg>
        555-014-2287
      </li>
      <li>
        <svg class="contact-icon" viewBox="0 0 30 30" aria-hidden="true">
          <circle cx="15" cy="15" r="15" fill="var(--red)"/>
          <rect x="7.5" y="10" width="15" height="10" fill="var(--white)"/>
          <path d="M7.5 10l7.5 6 7.5-6" fill="none" stroke="var(--red)" stroke-width="1.4"/>
        </svg>
        dale@copperleafroofing.co
      </li>
    </ul>
  </section>
</body>
</html>
```